RM Tomás Ledesma (Business Card)

Hi designers, in this work, I'm looking for an sophisticated stylish, elegant and proffesional personal card. We have a laboratory of pathology automated, with equipments high quality.
In this web the designers, have created my business logo, the name is "RM Tomás Ledesma"
In our lab, we principal work is to prepare the biopsies for further diagnostic of diseases like cancer, tumors, etc.
I need that the first face, only having my complete logo (Rm Tomás Ledesma, Laboratorio de procesamiento Histologico)
The overleaf, could repeat the same logo, like water logo.
In this face, I need to say: My full data:

Técnico en Anatomía Patológica
Tomás Ledesma Urquiza M.P 48213
Av. Duarte Quirós 817 - 2do piso - Instituto Brandsen.
Córdoba, Argentina
(0351) 158246093
ledesma.tomas@correoviva.com.ar

with respect the colors of card, use your imagination, the original logo color is violet, I haven't chosen a color base for the card.

attached pictures are examples of cards I like your DESIGN.
Attached too, the original logo to my company.

the size of card are:
horizontal: 9cm
vertical: 5,5cm

any question that you have, not doubt to question me,
Hand to work!

Industry/Entity Type

Laboratory

Requirements
Must have
• designers sophisticated, not simples, like show the images attached

```html
<!DOCTYPE html>
<html lang="es">
<head>
<meta charset="utf-8">
<title>Tomás Ledesma – Papelería</title>
<link rel="stylesheet" href="https://fonts.googleapis.com/css2?family=Montserrat:wght@400;600;700&family=PT+Sans+Narrow:wght@400;700&display=swap">
<style>
  :root {
    --backdrop: #2e2521;
    --violet: #652f8d;
    --violet-light: #7b45a6;
    --violet-dark: #4f2470;
    --grey-band: #7a7a7c;
    --card-white: #f1f0f3;
    --ink-violet: #4a2068;
    --ink-grey: #8a8a8c;
    --white: #ffffff;
  }
  * { margin: 0; padding: 0; box-sizing: border-box; }
  html, body { width: 1200px; height: 1181px; overflow: hidden; }
  body { background: var(--backdrop); position: relative; font-family: "Montserrat", sans-serif; }

  .letterhead {
    position: absolute; left: 168px; top: 187px; width: 863px; height: 526px;
    border-radius: 14px 14px 0 0; overflow: hidden;
    background: radial-gradient(ellipse at 50% 40%, var(--violet-light), var(--violet) 70%);
  }
  .letterhead__top { position: absolute; left: 0; top: 0; width: 100%; height: 95px; background: var(--grey-band); display: flex; align-items: center; justify-content: center; }
  .letterhead__bottom { position: absolute; left: 0; bottom: 0; width: 100%; height: 10px; background: var(--grey-band); }
  .mark-small { font-weight: 600; font-size: 15px; letter-spacing: 4px; color: var(--white); display: flex; align-items: center; gap: 8px; }
  .mark-small::before { content: ""; width: 8px; height: 8px; border-radius: 50%; background: var(--white); }

  .lockup { position: absolute; left: 0; width: 100%; text-align: center; color: var(--white); }
  .lockup__name { font-weight: 400; letter-spacing: 6px; text-transform: uppercase; display: inline-block; border-bottom: 1px solid var(--white); }
  .lockup__tagline { font-family: "PT Sans Narrow", sans-serif; text-transform: uppercase; }
  .letterhead .lockup { top: 300px; }
  .letterhead .lockup__name { font-size: 15px; padding: 0 14px 4px; }
  .letterhead .lockup__tagline { font-size: 19px; margin-top: 4px; }

  .letterhead__info { position: absolute; bottom: 20px; font-size: 9px; font-weight: 700; color: var(--white); line-height: 11px; }
  .letterhead__info--left { left: 28px; }
  .letterhead__info--right { right: 28px; }

  .card { position: absolute; top: 749px; width: 412px; height: 236px; border-radius: 16px; overflow: hidden; }
  .card--front { left: 168px; background: radial-gradient(ellipse at 50% 45%, #8a5bb0, var(--violet-dark) 75%); }
  .card--front .lockup { top: 110px; }
  .card--front .lockup__name { font-size: 13px; padding: 0 12px 3px; }
  .card--front .lockup__tagline { font-size: 16px; margin-top: 4px; }

  .card--back { left: 620px; width: 411px; background: var(--violet-dark); }
  .card--back__face { position: absolute; left: 0; top: 29px; width: 100%; height: 179px; background: radial-gradient(ellipse at 50% 50%, #ffffff, var(--card-white) 70%); }
  .card--back__watermark { position: absolute; left: 168px; top: 40px; width: 76px; height: 76px; border-radius: 50%; border: 3px solid rgba(101,47,141,0.12); }
  .card__name { position: absolute; top: 72px; width: 100%; text-align: center; font-weight: 700; font-size: 14px; color: var(--ink-violet); }
  .card__role { position: absolute; top: 92px; width: 100%; text-align: center; font-weight: 700; font-size: 9px; color: var(--ink-violet); }
  .card__contact { position: absolute; top: 146px; left: 0; width: 100%; display: flex; justify-content: center; font-size: 6.5px; font-weight: 600; color: var(--ink-violet); line-height: 8px; }
  .card__contact-col--left { text-align: right; padding-right: 6px; border-right: 1px solid var(--ink-violet); }
  .card__contact-col--right { padding-left: 6px; }
</style>
</head>
<body>
  <section class="letterhead">
    <div class="letterhead__top"><span class="mark-small">TOMÁS LEDESMA</span></div>
    <div class="lockup">
      <div class="lockup__name">Tomás Ledesma</div>
      <div class="lockup__tagline">Laboratorio de procesamiento histologico</div>
    </div>
    <p class="letterhead__info letterhead__info--left">Av. Duarte Quirós 817 - 2do piso - Instituto Brandsen.<br>Córdoba, Argentina</p>
    <p class="letterhead__info letterhead__info--right">(0351) 158246093<br>ledesma.tomas@correoviva.com.ar</p>
    <div class="letterhead__bottom"></div>
  </section>

  <section class="card card--front">
    <div class="lockup">
      <div class="lockup__name">Tomás Ledesma</div>
      <div class="lockup__tagline">Laboratorio de procesamiento histologico</div>
    </div>
  </section>

  <section class="card card--back">
    <div class="card--back__face">
      <div class="card--back__watermark"></div>
      <p class="card__name">Tomás Ledesma Urquiza</p>
      <p class="card__role">Técnico en Anatomía Patológica</p>
      <div class="card__contact">
        <div class="card__contact-col--left">Av. Duarte Quirós 817<br>2do piso - Instituto Brandsen<br>Córdoba, Argentina</div>
        <div class="card__contact-col--right">(0351) 158246093<br>ledesma.tomas@correoviva.com.ar<br>M.P 48213</div>
      </div>
    </div>
  </section>
</body>
</html>
```